LM-Steuerberatung WordPress Site fully implemented (tax advisor)

Hello!
I need a little Wordpress Site for my newly founded Tax-Advisor Company.
I am a one-man Office advising in the area of Crypto-Currency.
PLEASE only provide a Design, if you can also Implement a WP-Site afterwards on an existing Webspace.

Please find the Content and Website-Description in the attached Document

Language for the Website is German (for now)

Target Market(s)

Tax-Advisory (specialized in Crypto Currency)

Coding

Coded - Design and coding required

Number of Pages Required

5+ page

Font styles to use
Sans Serif

Requirements
Must have
• Wordpress Implementation afterwards - Details according to attached Project Information Document

```html
<!DOCTYPE html>
<html lang="de">
<head>
<meta charset="utf-8">
<title>LM-Steuerberatung</title>
<link rel="stylesheet" href="https://fonts.googleapis.com/css2?family=Poppins:wght@400;500;600;700&family=Fira+Sans:wght@300;400&display=swap">
<style>
  :root {
    --navy: #1b2a3d;
    --white: #ffffff;
    --ink: #1f2a36;
    --pink: #ff2fc1;
    --violet: #6a1fb8;
    --deep: #2a0a5e;
  }
  * { margin: 0; padding: 0; box-sizing: border-box; }
  html, body { width: 1200px; height: 857px; overflow: hidden; }
  body { font-family: "Poppins", sans-serif; background: var(--white); position: relative; }

  .site-header {
    position: absolute; left: 0; top: 0; width: 1200px; height: 94px;
    background: var(--white);
  }
  .brand {
    position: absolute; left: 113px; top: 28px; height: 38px;
    display: flex; align-items: center; gap: 10px;
    font-weight: 600; font-size: 17px; letter-spacing: 0.5px; color: var(--navy);
  }
  .brand-mark { width: 26px; height: 26px; background: var(--navy); }
  .main-nav {
    position: absolute; top: 38px; left: 0;
    font-family: "Fira Sans", sans-serif; font-size: 15px; color: var(--ink);
  }
  .main-nav a { position: absolute; white-space: nowrap; color: inherit; text-decoration: none; }
  .main-nav svg { vertical-align: middle; margin-left: 3px; }

  .hero {
    position: absolute; left: 0; top: 94px; width: 1200px; height: 703px; overflow: hidden;
  }
  .hero-art {
    position: absolute; inset: 0;
    background:
      radial-gradient(ellipse 380px 300px at 640px 340px, #ffc6f2 0%, rgba(255,90,220,0.8) 40%, rgba(255,47,193,0) 75%),
      radial-gradient(ellipse 220px 220px at 830px 290px, rgba(255,230,250,0.9) 0%, rgba(255,160,235,0.5) 45%, rgba(255,160,235,0) 75%),
      linear-gradient(180deg, #3a0f7a 0%, #b0179e 22%, #e52bb8 45%, #a51aa8 62%, #5a1aa0 78%, #2a0a5e 100%);
  }
  .hero-title {
    position: absolute; left: 109px; top: 248px; width: 600px;
    font-weight: 700; font-size: 50px; line-height: 69px; color: var(--white);
  }
  .hero-lead {
    position: absolute; left: 109px; top: 304px; width: 520px;
    font-family: "Fira Sans", sans-serif; font-weight: 300; font-size: 15px; line-height: 26px; color: var(--white);
  }
  .hero-button {
    position: absolute; left: 109px; top: 390px; width: 266px; height: 66px;
    background: var(--navy); border: 1px solid var(--white); border-radius: 5px;
    color: var(--white); font-weight: 600; font-size: 15px;
    display: flex; align-items: center; justify-content: center;
    box-shadow: 0 6px 12px rgba(0,0,0,0.3);
  }
  .steps { position: absolute; left: 111px; top: 0; list-style: none; }
  .step {
    position: absolute; left: 0; width: 900px; height: 48px;
    display: flex; align-items: center;
  }
  .step-number {
    width: 48px; height: 48px; border-radius: 50%;
    background: radial-gradient(circle at 40% 35%, #ffffff 0%, #e4e4e8 60%, #b9b9c2 100%);
    box-shadow: 2px 4px 6px rgba(0,0,0,0.45);
    display: flex; align-items: center; justify-content: center;
    font-weight: 600; font-size: 16px; color: var(--navy);
  }
  .step-text {
    margin-left: 22px; font-weight: 600; font-size: 16.5px; color: var(--white); white-space: nowrap;
  }

  .site-footer {
    position: absolute; left: 0; top: 797px; width: 1200px; height: 60px;
    background: var(--navy); color: var(--white);
    display: flex; align-items: center; justify-content: center;
    font-size: 15px;
  }
  .site-footer .sep { margin: 0 16px; }
</style>
</head>
<body>
  <header class="site-header">
    <div class="brand"><span class="brand-mark"></span>LM STEUERBERATUNG</div>
    <nav class="main-nav">
      <a style="left:589px">Home</a>
      <a style="left:670px">Leistungen<svg width="10" height="6" viewBox="0 0 10 6"><path d="M1 1l4 4 4-4" fill="none" stroke="#1f2a36" stroke-width="1.3"/></svg></a>
      <a style="left:800px">Über mich</a>
      <a style="left:910px">Kontakt</a>
      <a style="left:1004px">Impressum</a>
    </nav>
  </header>

  <section class="hero">
    <div class="hero-art" role="img" aria-label="Retro-Synthwave-Landschaft in Pink und Violett mit Gitterbergen und leuchtender Kryptomünze"></div>
    <h1 class="hero-title" style="top:163px">Willkommen bei LM Steuerberatung!</h1>
    <p class="hero-lead" style="top:304px">Ihrem Spezialisten bei allen steuerlichen Themen rund um Einkünfte &amp; Vermögen aus Krypto-Assets.</p>
    <a class="hero-button">Weiter zu unseren Leistungen</a>
    <ol class="steps">
      <li class="step" style="top:500px"><span class="step-number">01</span><span class="step-text">Dann mach ich eine Schweizer Holding-Gesellschaft– dort zahlt man fast keine Steuern</span></li>
      <li class="step" style="top:563px"><span class="step-number">02</span><span class="step-text">Dann melde ich einfach meinen Hauptwohnsitz in Österreich ab</span></li>
      <li class="step" style="top:623px"><span class="step-number">03</span><span class="step-text">Dann lass ich meine Kryptos auf einer Börse in Singapur, dort ist das steuerfrei</span></li>
    </ol>
  </section>

  <footer class="site-footer">
    <span>©Copyrights 2022 LM-Steuerberatung</span><span class="sep">|</span><span>All Rights Reserved</span>
  </footer>
</body>
</html>
```